Suds Haven Laundromat Wordpress Design

We need a Wordpress website design for our laundromat, Suds Haven Atlanta, at www.sudshavenatlanta-example.com. We would like to have 6 pages: Home, About Us, Services, Locations, Reviews and Contact us. We will provide content for the text on each page. What we do: We are a full service laundromat that provides dry cleaning drop off, professional laundry services, wash dry fold and self service laundry to the local community. We would like to use the color scheme from our logo to convey a warm, safe, and bright business that caters to its diverse community.
Updates

I like the structure of this laundromat website: http://www.washtroveusa-example.com/ Using my logo and color scheme in the above referenced website is what. Am looking for. The photos attached to the project with the female model should be used as a primary focus and supplemented by actual photos of the equipment.

Target Market(s)

Our target market is a diverse group of people from Midtown Atlanta - LGBTQ community /Locals/Regulars that have been coming to laundromat for 30 years.

Industry/Entity Type

Laundromat

Coding

Coded - Design and coding required

Number of Pages Required

5+ page

Font styles to use
Sans Serif

Colors
0054AA
0677BA
7BADD7
CADEEF
E8F1F8

Requirements
Must have
• Feature this video on the main page: https://videohost-example.com/xq7Rm2bPz4k

```html
<!DOCTYPE html>
<html lang="en">
<head>
<meta charset="utf-8">
<title>Suds Haven Atlanta – About Us</title>
<link rel="stylesheet" href="https://fonts.googleapis.com/css2?family=Bebas+Neue&family=Montserrat:wght@400;500;600;700&display=swap">
<style>
  :root {
    --blue-deep: #0054AA;
    --blue-mid: #0677BA;
    --blue-bright: #12a6e0;
    --blue-soft: #7BADD7;
    --blue-pale: #CADEEF;
    --ink: #2b2b2b;
    --section-tint: #f1f5f8;
    --card: #e3eaee;
    --footer: #2f4565;
    --footer-line: #4b6182;
    --white: #ffffff;
  }
  * { margin: 0; padding: 0; box-sizing: border-box; }
  html, body { width: 700px; height: 1200px; overflow: hidden; background: var(--white); }
  body { position: relative; font-family: "Montserrat", sans-serif; color: var(--ink); }
  .abs { position: absolute; }

  /* header */
  .site-header { position: absolute; left: 0; top: 0; width: 700px; height: 44px; background: var(--white); z-index: 2; }
  .brand { position: absolute; left: 60px; top: 12px; display: flex; align-items: center; gap: 5px;
    font-weight: 700; font-size: 15px; color: var(--blue-deep); letter-spacing: 0.2px; }
  .brand-dot { width: 9px; height: 9px; border-radius: 50%; background: var(--blue-deep); }
  .main-nav a { position: absolute; top: 20px; font-size: 7.2px; font-weight: 500; color: var(--ink); text-decoration: none; letter-spacing: 0.2px; }
  .main-nav a.is-active { font-weight: 600; }
  .nav-underline { left: 290px; top: 42px; width: 39px; height: 2px; background: var(--blue-deep); }
  .nav-divider { left: 600px; top: 11px; width: 1px; height: 22px; background: var(--blue-deep); }
  .social-mini { top: 18px; width: 7px; height: 7px; border-radius: 50%; background: var(--ink); }

  /* hero */
  .hero { left: 0; top: 44px; width: 700px; height: 245px; }

  .breadcrumb { left: 95px; top: 294px; font-size: 7.2px; font-weight: 500; }
  .breadcrumb .current { color: var(--blue-deep); font-weight: 600; }

  /* about */
  .about-visual { left: 92px; top: 380px; width: 206px; height: 210px; }
  .section-title { font-family: "Bebas Neue", sans-serif; font-size: 20px; color: #333; letter-spacing: 0.2px; line-height: 1; }
  .section-title span { color: var(--blue-mid); }
  .title-rule { height: 2px; background: var(--blue-bright); }
  .about-title { left: 334px; top: 372px; }
  .about-copy { left: 334px; top: 406px; width: 275px; font-size: 7.6px; line-height: 15.7px; }
  .about-copy p + p { margin-top: 2.5px; }
  .btn { left: 334px; top: 541px; width: 87px; height: 25px; background: var(--blue-bright); color: var(--white);
    font-size: 7.4px; font-weight: 600; display: flex; align-items: center; justify-content: center; border-radius: 1px; }

  /* why choose */
  .why { left: 0; top: 632px; width: 700px; height: 262px; background: var(--section-tint); }
  .why-title { left: 0; top: 677px; width: 700px; text-align: center; }
  .card { width: 164px; height: 61px; background: var(--card); border-radius: 3px; padding: 11px 8px 0 24px;
    font-size: 9px; line-height: 15.2px; color: var(--ink); }
  .card svg { position: absolute; left: 7px; top: 13px; }

  /* footer */
  .site-footer { left: 0; top: 894px; width: 700px; height: 306px; background: var(--footer); color: var(--white); }
  .footer-brand { left: 0; top: 945px; width: 700px; display: flex; justify-content: center; align-items: center; gap: 7px;
    font-weight: 700; font-size: 26px; color: var(--white); }
  .footer-brand .brand-dot { width: 14px; height: 14px; background: var(--white); }
  .footer-rule { height: 1px; background: var(--footer-line); }
  .footer-nav a { position: absolute; top: 1028px; font-size: 9px; color: var(--white); text-decoration: none; }
  .footer-social { top: 1025px; width: 18px; height: 18px; border-radius: 50%; background: var(--white); }
  .contact-line { font-size: 8px; line-height: 14.5px; color: var(--white); }
  .delivery { color: var(--blue-bright); }
  .copyright { left: 0; top: 1163px; width: 700px; text-align: center; font-size: 7.2px; color: #dfe6ef; }
  .copyright strong { color: var(--white); font-weight: 600; }
</style>
</head>
<body>

<header class="site-header">
  <div class="brand"><span class="brand-dot"></span>Suds Haven</div>
  <nav class="main-nav">
    <a style="left:243px" href="#">HOME</a>
    <a style="left:290px" class="is-active" href="#">ABOUT US</a>
    <a style="left:353px" href="#">SERVICES</a>
    <a style="left:413px" href="#">LOCATION</a>
    <a style="left:482px" href="#">REVIEWS</a>
    <a style="left:540px" href="#">CONTACT US</a>
  </nav>
  <div class="abs nav-underline"></div>
  <div class="abs nav-divider"></div>
  <span class="abs social-mini" style="left:612px"></span>
  <span class="abs social-mini" style="left:627px"></span>
</header>

<svg class="abs hero" viewBox="0 0 700 245" role="img" aria-label="Storefront of the laundromat at night, seen through glass with washers, seating and plants inside">
  <defs>
    <linearGradient id="heroTone" x1="0" y1="0" x2="1" y2="1">
      <stop offset="0" stop-color="#6f6d52"/>
      <stop offset="0.45" stop-color="#d9d46a"/>
      <stop offset="1" stop-color="#5f6a3c"/>
    </linearGradient>
  </defs>
  <rect width="700" height="245" fill="url(#heroTone)"/>
  <path d="M0 197 Q350 292 700 190 L700 245 L0 245 Z" fill="var(--white)"/>
  <path d="M0 197 Q350 292 700 190 L700 193 Q350 280 0 206 Z" fill="#ffffff"/>
  <path d="M0 196 Q330 285 670 203 Q350 300 0 206 Z" fill="var(--blue-deep)"/>
</svg>

<div class="abs breadcrumb">HOME / <span class="current">ABOUT US</span></div>

<svg class="abs about-visual" viewBox="0 0 206 210" role="img" aria-label="Round photo of a woman in a blue dress seated before a row of front-loading washers">
  <defs>
    <linearGradient id="portraitTone" x1="0" y1="0" x2="0" y2="1">
      <stop offset="0" stop-color="#cfe6e6"/>
      <stop offset="0.5" stop-color="#bdb8ab"/>
      <stop offset="1" stop-color="#d8d4cc"/>
    </linearGradient>
  </defs>
  <circle cx="101" cy="104" r="90" fill="url(#portraitTone)"/>
  <path d="M160 188 A98 98 0 1 1 156 24" fill="none" stroke="var(--blue-mid)" stroke-width="5"/>
  <path d="M156 24 A98 98 0 0 1 198 62" fill="none" stroke="var(--blue-mid)" stroke-width="6"/>
</svg>

<h1 class="abs section-title about-title">About <span>Us</span></h1>
<div class="abs title-rule" style="left:334px;top:395px;width:26px"></div>
<div class="abs about-copy">
  <p>Suds Haven is family-owned laundromat that has been serving Midtown, GA for over 45 years. We are proud to offer high quality and convenient services to the area residents and business owners and strive to keep our customers clothing in tip top shape.</p>
  <p>Whether you have commercial laundry needs, are washing clothes for your family, or want to relax that weekend and have us pick up and wash/dry/fold for you, the professionals at Suds Haven are ready to meet your goals.</p>
</div>
<div class="abs btn">Contact Us Today</div>

<section class="abs why"></section>
<h2 class="abs section-title why-title">Why <span>Choose Us</span></h2>
<div class="abs title-rule" style="left:337px;top:702px;width:26px"></div>

<div class="abs card" style="left:94px;top:717px"><svg width="11" height="11" viewBox="0 0 11 11"><circle cx="5.5" cy="5.5" r="4.5" fill="none" stroke="var(--blue-mid)" stroke-width="1"/><path d="M3 5.6 L5 7.4 L10 1.8" fill="none" stroke="var(--blue-mid)" stroke-width="1.2"/></svg>In Business over 45 years</div>
<div class="abs card" style="left:268px;top:717px"><svg width="11" height="11" viewBox="0 0 11 11"><circle cx="5.5" cy="5.5" r="4.5" fill="none" stroke="var(--blue-mid)" stroke-width="1"/><path d="M3 5.6 L5 7.4 L10 1.8" fill="none" stroke="var(--blue-mid)" stroke-width="1.2"/></svg>Voted "BEST COIN LAUNDRY" - Multiple years</div>
<div class="abs card" style="left:442px;top:717px"><svg width="11" height="11" viewBox="0 0 11 11"><circle cx="5.5" cy="5.5" r="4.5" fill="none" stroke="var(--blue-mid)" stroke-width="1"/><path d="M3 5.6 L5 7.4 L10 1.8" fill="none" stroke="var(--blue-mid)" stroke-width="1.2"/></svg>One of Atlanta's First, Finest, &amp; Friendliest Coin Laundries</div>
<div class="abs card" style="left:94px;top:787px"><svg width="11" height="11" viewBox="0 0 11 11"><circle cx="5.5" cy="5.5" r="4.5" fill="none" stroke="var(--blue-mid)" stroke-width="1"/><path d="M3 5.6 L5 7.4 L10 1.8" fill="none" stroke="var(--blue-mid)" stroke-width="1.2"/></svg>The best Wash-Dry-Fold in Town</div>
<div class="abs card" style="left:268px;top:787px"><svg width="11" height="11" viewBox="0 0 11 11"><circle cx="5.5" cy="5.5" r="4.5" fill="none" stroke="var(--blue-mid)" stroke-width="1"/><path d="M3 5.6 L5 7.4 L10 1.8" fill="none" stroke="var(--blue-mid)" stroke-width="1.2"/></svg>Cool - Comfortable - Clean</div>
<div class="abs card" style="left:442px;top:787px"><svg width="11" height="11" viewBox="0 0 11 11"><circle cx="5.5" cy="5.5" r="4.5" fill="none" stroke="var(--blue-mid)" stroke-width="1"/><path d="M3 5.6 L5 7.4 L10 1.8" fill="none" stroke="var(--blue-mid)" stroke-width="1.2"/></svg>Over 50 Well Maintained Machines</div>

<footer class="abs site-footer"></footer>
<div class="abs footer-brand"><span class="brand-dot"></span>Suds Haven</div>
<div class="abs footer-rule" style="left:181px;top:1010px;width:338px"></div>
<nav class="footer-nav">
  <a style="left:148px" href="#">Home</a>
  <a style="left:197px" href="#">About Us</a>
  <a style="left:260px" href="#">Services</a>
  <a style="left:320px" href="#">Location</a>
  <a style="left:385px" href="#">Reviews</a>
  <a style="left:445px" href="#">Contact Us</a>
</nav>
<span class="abs footer-social" style="left:512px"></span>
<span class="abs footer-social" style="left:539px"></span>
<div class="abs footer-rule" style="left:181px;top:1058px;width:338px"></div>

<svg class="abs" style="left:143px;top:1071px" width="11" height="13" viewBox="0 0 11 13"><circle cx="5.5" cy="5.5" r="4.5" fill="none" stroke="#cfd8e4" stroke-width="0.9"/><circle cx="5.5" cy="5.5" r="1.6" fill="none" stroke="#cfd8e4" stroke-width="0.9"/><path d="M3 9.5 L5.5 12.5 L8 9.5" fill="none" stroke="#cfd8e4" stroke-width="0.9"/></svg>
<div class="abs contact-line" style="left:162px;top:1072px;width:190px">Brightwater Plaza, 2280 Marlow Ave NE., # 112, Atlanta, GA 30399</div>
<svg class="abs" style="left:143px;top:1105px" width="11" height="11" viewBox="0 0 11 11"><path d="M2 1 L4 1 L5 3.5 L3.6 4.6 Q4.8 7 6.4 7.4 L7.5 6 L10 7 L10 9 Q9 10.5 7 10 Q1.5 8 1 3 Q1 1.5 2 1 Z" fill="none" stroke="#cfd8e4" stroke-width="0.8"/></svg>
<div class="abs contact-line" style="left:161px;top:1104px">(404) 555-0142</div>

<div class="abs contact-line delivery" style="left:356px;top:1072px">Delivery Available* please contact us for details</div>
<div class="abs contact-line" style="left:356px;top:1091px">Covid 19 hours - open 7 days a week 8 am to 8 pm<br>Last wash begins 6:30 pm</div>

<div class="abs footer-rule" style="left:94px;top:1137px;width:512px"></div>
<div class="abs copyright">Copyright © 2021 <strong>Suds Haven Atlanta</strong>. All Rights Reserved.</div>

</body>
</html>
```